Property development business card design

New build residential property developers. I want a professional look but customer friendly so not too corporate. I'm not sure what logo will look best so open to designs with either. Thank you

Also i don't want both names on one card its 2 names for 2 different cards but with the same design.

Industry/Entity Type

Residential

Contact Information for Business Card

KTR Developments Ltd,
58 Fennel Lane,
Ipswich,
Suffolk,
IP7 4WD

Property Research Manager
Morven Tadlock

Managing Director
Dilan Perriwick

```html
<!DOCTYPE html>
<html lang="en">
<head>
<meta charset="utf-8">
<title>KTR Developments – Business Card</title>
<link href="https://fonts.googleapis.com/css2?family=Exo+2:wght@400;500;700&display=swap" rel="stylesheet">
<style>
  :root {
    --bg: #b9b9b9;
    --card: #ffffff;
    --brand-blue: #1f7fc4;
    --brand-green: #8cc63f;
    --brand-grey: #8d8d8d;
    --text: #4a4a4a;
  }
  * { margin: 0; padding: 0; box-sizing: border-box; }
  html, body { width: 1200px; height: 894px; overflow: hidden; }
  body {
    background: var(--bg);
    font-family: "Exo 2", Arial, sans-serif;
    display: flex;
    align-items: center;
    justify-content: center;
    gap: 40px;
  }
  .card {
    position: relative;
    width: 540px;
    height: 309px;
    background: var(--card);
    box-shadow: 0 6px 18px rgba(0,0,0,0.18);
    overflow: hidden;
  }

  /* Brand lockup */
  .brand { position: absolute; display: flex; align-items: center; gap: 12px; }
  .brand-dot { border-radius: 50%; background: var(--brand-blue); flex: none; }
  .brand-name {
    color: var(--brand-grey);
    font-weight: 700;
    text-transform: uppercase;
    letter-spacing: 0.04em;
  }

  /* Back face */
  .card-back .brand { left: 50%; top: 50%; transform: translate(-50%, -50%); }
  .card-back .brand-dot { width: 78px; height: 78px; }
  .card-back .brand-name { font-size: 30px; }

  /* Front face */
  .card-front .brand { left: 36px; top: 28px; }
  .card-front .brand-dot { width: 58px; height: 58px; }
  .card-front .brand-name { font-size: 22px; }

  .holder { position: absolute; left: 36px; top: 108px; }
  .holder-name {
    color: var(--brand-blue);
    font-size: 19px;
    font-weight: 500;
    text-transform: uppercase;
    letter-spacing: 0.08em;
  }
  .holder-role {
    color: var(--text);
    font-size: 11px;
    text-transform: uppercase;
    letter-spacing: 0.12em;
    margin-top: 2px;
  }

  .contacts {
    position: absolute;
    list-style: none;
    font-size: 11.5px;
    color: var(--text);
    letter-spacing: 0.04em;
  }
  .contacts li { display: flex; align-items: flex-start; gap: 7px; margin-bottom: 6px; line-height: 1.35; }
  .contacts svg { width: 12px; height: 12px; flex: none; margin-top: 1px; }
  .contacts-location { left: 36px; top: 170px; }
  .contacts-direct { left: 330px; top: 170px; }

  .accent-bar {
    position: absolute;
    left: 0;
    bottom: 46px;
    width: 88%;
    height: 8px;
    background: linear-gradient(90deg, var(--brand-blue) 0%, #5aa8dd 58%, var(--brand-green) 58%, var(--brand-green) 100%);
  }
</style>
</head>
<body>

  <section class="card card-back" aria-label="Business card, back">
    <div class="brand">
      <span class="brand-dot"></span>
      <span class="brand-name">KTR Developments</span>
    </div>
  </section>

  <section class="card card-front" aria-label="Business card, front">
    <div class="brand">
      <span class="brand-dot"></span>
      <span class="brand-name">KTR Developments</span>
    </div>

    <div class="holder">
      <p class="holder-name">Dilan Perriwick</p>
      <p class="holder-role">Managing Director</p>
    </div>

    <ul class="contacts contacts-location">
      <li>
        <svg viewBox="0 0 12 12" aria-hidden="true"><path d="M6 0.5a4 4 0 0 0-4 4c0 3 4 7 4 7s4-4 4-7a4 4 0 0 0-4-4zm0 5.6a1.6 1.6 0 1 1 0-3.2 1.6 1.6 0 0 1 0 3.2z" fill="var(--brand-blue)"/></svg>
        <span>58 Fennel Lane<br>Ipswich IP7 4WD</span>
      </li>
      <li>
        <svg viewBox="0 0 12 12" aria-hidden="true"><g fill="none" stroke="var(--brand-blue)" stroke-width="1"><circle cx="6" cy="6" r="5"/><ellipse cx="6" cy="6" rx="2.2" ry="5"/><path d="M1 6h10M2 3.2h8M2 8.8h8"/></g></svg>
        <span>www.ktrhomes.co.uk</span>
      </li>
    </ul>

    <ul class="contacts contacts-direct">
      <li>
        <svg viewBox="0 0 12 12" aria-hidden="true"><path d="M2.6 0.8l1.8 0 1 2.6-1.3 1c0.6 1.4 1.6 2.4 3 3l1-1.3 2.6 1v1.8c0 0.7-0.6 1.2-1.3 1.2C4.6 10 1.4 6.8 1.4 2.1c0-0.7 0.5-1.3 1.2-1.3z" fill="var(--brand-blue)"/></svg>
        <span>01473 555 0192</span>
      </li>
      <li>
        <svg viewBox="0 0 12 12" aria-hidden="true"><rect x="3" y="0.5" width="6" height="11" rx="1" fill="none" stroke="var(--brand-blue)" stroke-width="1.1"/><circle cx="6" cy="9.6" r="0.7" fill="var(--brand-blue)"/></svg>
        <span>07700 555 0148</span>
      </li>
      <li>
        <svg viewBox="0 0 12 12" aria-hidden="true"><rect x="0.5" y="2" width="11" height="8" fill="var(--brand-blue)"/><path d="M0.8 2.4L6 6.6l5.2-4.2" fill="none" stroke="#fff" stroke-width="1"/></svg>
        <span>hello@ktrhomes.co.uk</span>
      </li>
    </ul>

    <div class="accent-bar"></div>
  </section>

</body>
</html>
```